Veranix - Solution provider in business consulting

Veranix is a swiss based company providing solutions for developing markets. The business covers various fields of business consulting, such as supply chain, product costs, quality management and manufacturing management. The Business operates in a efficient, straight and solution oriented manner.
The final design should communicate these characteristics. Asian people as well as as western people shall identify the qualities of the company at first sight.
The customer needs business cards with a simple view but an recognizable design, printed in high quality. Engraved elements such as the globe or simple words are possible.
Available colors are: (RAL)
102/102/102
51/102/102
153/204/153
255/102/51
Font: Calibri

```html
<!DOCTYPE html>
<html lang="en">
<head>
<meta charset="utf-8">
<title>Veranix – Business Cards</title>
<link rel="stylesheet" href="https://fonts.googleapis.com/css2?family=Carlito:wght@400;700&display=swap">
<style>
  :root {
    --bg: #e6e3de;
    --white: #ffffff;
    --grey-dark: #555555;
    --grey-main: #666666;
    --grey-mid: #7a7a7a;
    --grey-light: #9a9a9a;
    --grey-pale: #d4d4d4;
    --text-light: #ffffff;
  }
  * { box-sizing: border-box; margin: 0; padding: 0; }
  html, body {
    width: 1200px;
    height: 950px;
    overflow: hidden;
    background: var(--bg);
    font-family: "Carlito", "Calibri", sans-serif;
  }
  .sheet {
    position: relative;
    width: 1200px;
    height: 950px;
  }
  .card {
    position: absolute;
    left: 220px;
    width: 760px;
    height: 434px;
    overflow: hidden;
    box-shadow: 0 6px 18px rgba(0, 0, 0, 0.18);
  }

  /* Front */
  .card-front {
    top: 24px;
    background: linear-gradient(90deg,
      var(--white) 0%, var(--white) 52%,
      var(--grey-light) 60%, var(--grey-mid) 75%, var(--grey-main) 100%);
  }
  .brand-name {
    position: absolute;
    left: 44px;
    top: 34px;
    font-size: 60px;
    font-weight: 400;
    color: var(--grey-main);
    letter-spacing: 1px;
  }
  .globe-artwork {
    position: absolute;
    left: 0;
    top: 190px;
    width: 430px;
    height: 244px;
    background: linear-gradient(160deg, var(--grey-light) 0%, var(--grey-main) 70%);
    border-top-right-radius: 60px;
  }
  .contact {
    position: absolute;
    right: 40px;
    top: 92px;
    text-align: right;
    color: var(--text-light);
  }
  .contact-name {
    font-size: 30px;
    font-weight: 700;
    line-height: 1.1;
  }
  .contact-role {
    font-size: 21px;
    margin-bottom: 42px;
  }
  .company-name {
    font-size: 21px;
    font-weight: 700;
  }
  .company-line {
    font-size: 21px;
    line-height: 1.25;
  }
  .company-line.country { margin-bottom: 14px; }
  .contact-row {
    display: flex;
    justify-content: flex-end;
    align-items: center;
    gap: 8px;
    font-size: 21px;
    line-height: 1.3;
  }
  .contact-icon {
    width: 20px;
    height: 20px;
    flex: none;
  }

  /* Back */
  .card-back {
    top: 494px;
    background: linear-gradient(120deg,
      var(--grey-dark) 0%, var(--grey-mid) 55%, var(--grey-main) 100%);
  }
  .back-artwork {
    position: absolute;
    left: 330px;
    top: 70px;
    width: 200px;
    height: 230px;
    background: linear-gradient(150deg, var(--grey-pale) 0%, var(--grey-light) 100%);
    border-radius: 8px;
  }
  .back-web {
    position: absolute;
    left: 330px;
    top: 318px;
    font-size: 24px;
    color: var(--grey-pale);
    letter-spacing: 1px;
  }
</style>
</head>
<body>
<main class="sheet">

  <section class="card card-front" aria-label="Business card front">
    <div class="brand-name">veranix</div>
    <div class="globe-artwork" role="img" aria-label="Engraved globe artwork showing Asia"></div>

    <div class="contact">
      <div class="contact-name">Marco Hefti</div>
      <div class="contact-role">CEO</div>
      <div class="company-name">Veranix GmbH</div>
      <div class="company-line">Lindenweg 14, 9100 Herisau</div>
      <div class="company-line country">Switzerland</div>

      <div class="contact-row">
        <span>+41 71 555 0142</span>
        <svg class="contact-icon" viewBox="0 0 20 20" aria-hidden="true">
          <path d="M4 7 Q10 2 16 7 L14 9 L12 7 L8 7 L6 9 Z" fill="#fff"/>
          <rect x="5" y="10" width="10" height="7" rx="1.5" fill="#fff"/>
        </svg>
      </div>
      <div class="contact-row">
        <span>+41 79 555 0187</span>
        <svg class="contact-icon" viewBox="0 0 20 20" aria-hidden="true">
          <rect x="6" y="2" width="8" height="16" rx="1.5" fill="#fff"/>
          <rect x="7.5" y="4" width="5" height="9" fill="#666"/>
        </svg>
      </div>
      <div class="contact-row">
        <span>marco.hefti@veranix.ch</span>
        <svg class="contact-icon" viewBox="0 0 20 20" aria-hidden="true">
          <rect x="2" y="5" width="16" height="11" rx="1" fill="#fff"/>
          <path d="M2.5 5.5 L10 11 L17.5 5.5" fill="none" stroke="#666" stroke-width="1.3"/>
        </svg>
      </div>
      <div class="contact-row">
        <span>www.veranix.ch</span>
        <svg class="contact-icon" viewBox="0 0 20 20" aria-hidden="true">
          <circle cx="10" cy="10" r="8" fill="#fff"/>
          <path d="M2 10 H18 M10 2 V18" stroke="#666" stroke-width="1.2"/>
        </svg>
      </div>
    </div>
  </section>

  <section class="card card-back" aria-label="Business card back">
    <div class="back-artwork" role="img" aria-label="Engraved globe artwork"></div>
    <div class="back-web">www.veranix.ch</div>
  </section>

</main>
</body>
</html>
```